The Quiet Lantern Business Card

I need a business card designed for The Quiet Lantern. The company provides on site support and education to end consumers in the ins and outs of all our digital devices. We advise on product purchase, installation, maintenance and troubleshooting. Anything from cordless phones to home networks.
My initial concept is double sided with the white logo on green on one side and contact details and a small logo on the flip side (logo package attached)
Contact Details:
Pablo Strand
Managing Director
PO Box 4
Marlow Heights, NSW 2091
Phone: 0438 559 106
email: pablo@quietlantern.com.au
web: www.quietlantern.com.au
Target Market(s)
Busy professionals and retired folks.
Industry/Entity Type
Education
Look and feel

```html
<!DOCTYPE html>
<html lang="en">
<head>
<meta charset="UTF-8">
<title>The Quiet Lantern – Business Card</title>
<link rel="stylesheet" href="https://fonts.googleapis.com/css2?family=Raleway:wght@400;600&display=swap">
<style>
  :root {
    --page: #eceae6;
    --card: #ffffff;
    --card-shade: #e4e6e7;
    --navy: #18324a;
    --green: #6cb33f;
    --ink: #18324a;
    --light-text: #ffffff;
  }
  * { box-sizing: border-box; margin: 0; padding: 0; }
  html, body {
    width: 1057px;
    height: 1200px;
    overflow: hidden;
    background: var(--page);
    font-family: "Raleway", sans-serif;
  }
  .sheet {
    position: relative;
    width: 1057px;
    height: 1200px;
  }
  .card {
    position: absolute;
    left: 178px;
    width: 700px;
    height: 400px;
    box-shadow: 0 6px 18px rgba(0,0,0,0.18);
    overflow: hidden;
  }
  .card--front { top: 120px; }
  .card--back { top: 660px; background: var(--card); }

  /* Front */
  .front-frame {
    position: absolute; inset: 0;
    background: var(--green);
    padding: 14px;
  }
  .front-frame__inner {
    width: 100%; height: 100%;
    border: 12px solid var(--navy);
    background: radial-gradient(ellipse at 45% 40%, var(--card) 40%, var(--card-shade) 100%);
    display: flex; align-items: center; justify-content: center;
  }

  .brand {
    display: flex; align-items: center; gap: 14px;
  }
  .brand__dot {
    width: 34px; height: 34px;
    border-radius: 50%;
    background: var(--green);
    flex: none;
  }
  .brand__name {
    font-weight: 400;
    color: var(--ink);
    letter-spacing: 0.04em;
    white-space: nowrap;
  }
  .brand--large .brand__name { font-size: 40px; }
  .brand--small .brand__dot { width: 24px; height: 24px; }
  .brand--small .brand__name { font-size: 28px; }

  /* Back */
  .back-shapes { position: absolute; inset: 0; }
  .back-brand { position: absolute; left: 150px; top: 88px; }

  .person {
    position: absolute; left: 34px; top: 258px;
    color: var(--light-text);
  }
  .person__name {
    font-size: 22px; font-weight: 600; letter-spacing: 0.08em;
  }
  .person__role {
    font-size: 12px; font-weight: 400; letter-spacing: 0.2em; margin-top: 3px;
  }

  .contact-list {
    position: absolute; list-style: none;
    color: var(--light-text); font-size: 11px; letter-spacing: 0.03em;
  }
  .contact-list li {
    display: flex; align-items: center; gap: 9px; height: 19px;
  }
  .contact-list__icon {
    width: 12px; height: 12px; background: var(--light-text); flex: none;
    display: flex; align-items: center; justify-content: center;
  }
  .contact-list__icon::after {
    content: ""; width: 5px; height: 5px; background: var(--navy);
  }
  .contact-list--details { left: 34px; top: 326px; }
  .contact-list--phones { left: 576px; top: 150px; }
</style>
</head>
<body>
<main class="sheet">

  <section class="card card--front" aria-label="Card front">
    <div class="front-frame">
      <div class="front-frame__inner">
        <div class="brand brand--large">
          <span class="brand__dot"></span>
          <span class="brand__name">The Quiet Lantern</span>
        </div>
      </div>
    </div>
  </section>

  <section class="card card--back" aria-label="Card back">
    <svg class="back-shapes" width="700" height="400" viewBox="0 0 700 400" aria-hidden="true">
      <rect x="500" y="0" width="12" height="400" fill="var(--navy)"/>
      <rect x="512" y="0" width="46" height="400" fill="var(--green)"/>
      <rect x="558" y="0" width="142" height="400" fill="var(--navy)"/>
      <polygon points="220,236 512,236 512,278 262,278" fill="var(--green)"/>
      <polygon points="0,244 214,244 258,290 512,290 512,400 0,400" fill="var(--navy)"/>
    </svg>

    <div class="brand brand--small back-brand">
      <span class="brand__dot"></span>
      <span class="brand__name">The Quiet Lantern</span>
    </div>

    <div class="person">
      <p class="person__name">PABLO STRAND</p>
      <p class="person__role">FOUNDER</p>
    </div>

    <ul class="contact-list contact-list--details">
      <li><span class="contact-list__icon"></span>PO Box 4, Marlow Heights, NSW 2091</li>
      <li><span class="contact-list__icon"></span>www.quietlantern.com.au</li>
      <li><span class="contact-list__icon"></span>pablo@quietlantern.com.au</li>
    </ul>

    <ul class="contact-list contact-list--phones">
      <li><span class="contact-list__icon"></span>0438 559 106</li>
      <li><span class="contact-list__icon"></span>02 9555 0142</li>
    </ul>
  </section>

</main>
</body>
</html>
```